New Business Card for Web Design/Internet Marketing Company

Looking for a great looking new business card. We are a 10 year old web design, internet marketing and website management company that works mostly with small businesses.

Our new card needs to better match the colors and style of our website, be bold, extremely usable and slightly edgy.

Target Market(s)

Small/Medium businesses that have websites

Industry/Entity Type

Internet

Requirements
Must have
• Front and back design, full color, rounded corners please

Must use the colors/style of our website (JPG provided)

INFO FOR CARDS (as readable as possible please)
Mark Lenner
President/CEO
mark@trelvanmedia.example
Phone: 520-381-7459
Toll Free: 866-381-7459
Address: 4315 W. Calloway Ave. Ste. 140, Tucson, AZ 85792

THINGS I WANT TO PROMOTE (if there is room):
1. Our Website - www.trelvanmedia.example

2. Social Media
Twitter: @trelvanmedia
Facebook: www.facebook.com/trelvanmedia

3. Our Services
Web Design
Internet Marketing
Website Management

```html
<!DOCTYPE html>
<html lang="en">
<head>
<meta charset="utf-8">
<title>Trelvan Media – Business Card</title>
<link href="https://fonts.googleapis.com/css2?family=Open+Sans:ital,wght@0,400;0,600;0,700;1,700&display=swap" rel="stylesheet">
<style>
  :root{
    --page:#e9ebee;
    --blue:#1a9fd6;
    --blue-light:#22b8ea;
    --blue-deep:#0d7fb3;
    --orange:#f47b20;
    --white:#ffffff;
    --ink:#5a5f66;
    --card-radius:28px;
  }
  *{box-sizing:border-box;margin:0;padding:0}
  html,body{width:1067px;height:1200px;overflow:hidden;background:var(--page);
    font-family:"Open Sans",Arial,sans-serif}
  .card{position:absolute;left:133px;width:800px;height:457px;border-radius:var(--card-radius);
    overflow:hidden;box-shadow:0 6px 18px rgba(0,0,0,.18)}
  .card--front{top:100px}
  .card--back{top:630px}
  .card svg{position:absolute;inset:0;width:100%;height:100%}
  .layer{position:absolute}

  /* brand lockup */
  .brand{display:flex;align-items:center;gap:16px}
  .brand__dot{width:54px;height:54px;border-radius:50%;background:var(--orange)}
  .brand__name{font-weight:700;font-size:54px;letter-spacing:-1px;line-height:1}
  .tagline{font-size:20px;font-weight:600;color:var(--ink)}

  /* front */
  .front-brand{left:60px;top:62px}
  .front-brand .brand__name{color:var(--blue)}
  .front-tagline{left:400px;top:132px}
  .holder{left:64px;top:300px;color:var(--white)}
  .holder__name{font-style:italic;font-weight:700;font-size:24px}
  .holder__title{font-size:16px;font-weight:600;margin-bottom:16px}
  .holder__address{font-size:16px;line-height:1.55}
  .contacts{left:468px;top:300px;color:var(--white);font-size:16px;line-height:1.6;list-style:none}
  .contacts__label{color:var(--orange);font-weight:700;display:inline-block;width:20px}

  /* back */
  .back-brand{left:0;right:0;top:62px;justify-content:center}
  .back-brand .brand__name{color:var(--white)}
  .back-tagline{left:0;right:0;top:130px;text-align:center;color:var(--white)}
  .services{left:0;right:0;top:180px;text-align:center;color:var(--white);font-size:17px;font-weight:600}
  .website{left:0;right:0;top:210px;text-align:center;color:var(--white);font-size:20px;letter-spacing:3px;font-weight:600}
  .social{display:flex;align-items:center;gap:12px;color:var(--blue);font-size:19px;font-weight:600;text-transform:uppercase;letter-spacing:.5px}
  .social__mark{width:24px;height:24px;border-radius:4px;background:var(--orange)}
  .social--facebook{left:50px;top:398px}
  .social--twitter{left:540px;top:308px}
</style>
</head>
<body>

<section class="card card--front" aria-label="Card front">
  <svg viewBox="0 0 800 457" aria-hidden="true">
    <defs>
      <linearGradient id="frontBand" x1="0" y1="0" x2="1" y2="1">
        <stop offset="0" stop-color="#1592cb"/>
        <stop offset=".5" stop-color="#22b8ea"/>
        <stop offset="1" stop-color="#0e86bd"/>
      </linearGradient>
    </defs>
    <rect width="800" height="457" fill="#ffffff"/>
    <path d="M0 252 Q400 312 800 232 L800 457 L0 457 Z" fill="url(#frontBand)"/>
    <path d="M290 262 Q560 288 800 220 L800 232 Q560 300 290 262 Z" fill="#f47b20"/>
  </svg>

  <div class="layer brand front-brand">
    <span class="brand__dot"></span>
    <span class="brand__name">Trelvan Media</span>
  </div>
  <div class="layer tagline front-tagline">Websites That Work</div>

  <div class="layer holder">
    <div class="holder__name">Mark Lenner</div>
    <div class="holder__title">President/CEO</div>
    <div class="holder__address">4315 W. Calloway Ave. Ste. 140,<br>Tucson, AZ 85792</div>
  </div>

  <ul class="layer contacts">
    <li><span class="contacts__label">p:</span> 520 381 7459</li>
    <li><span class="contacts__label">t:</span> 866 381 7459</li>
    <li><span class="contacts__label">e:</span> mark@trelvanmedia.example</li>
    <li><span class="contacts__label">w:</span> www.trelvanmedia.example</li>
  </ul>
</section>

<section class="card card--back" aria-label="Card back">
  <svg viewBox="0 0 800 457" aria-hidden="true">
    <defs>
      <radialGradient id="backGlow" cx=".45" cy=".35" r=".75">
        <stop offset="0" stop-color="#27b6e6"/>
        <stop offset=".6" stop-color="#1a9fd6"/>
        <stop offset="1" stop-color="#0d7fb3"/>
      </radialGradient>
    </defs>
    <rect width="800" height="457" fill="url(#backGlow)"/>
    <path d="M0 330 Q450 340 800 170 L800 186 Q450 356 0 342 Z" fill="#f47b20"/>
    <path d="M0 342 Q450 356 800 186 L800 457 L0 457 Z" fill="#ffffff"/>
  </svg>

  <div class="layer brand back-brand">
    <span class="brand__dot"></span>
    <span class="brand__name">Trelvan Media</span>
  </div>
  <div class="layer tagline back-tagline">Websites That Work</div>
  <div class="layer services">Web Design / Internet Marketing / Website Management</div>
  <div class="layer website">www.trelvanmedia.example</div>

  <div class="layer social social--twitter">
    <span class="social__mark"></span><span>@trelvanmedia</span>
  </div>
  <div class="layer social social--facebook">
    <span class="social__mark"></span><span>/trelvanmedia</span>
  </div>
</section>

</body>
</html>
```